Bright Step Path Flyer, eyecatching

Hi,
To give you an idea of the business for design purposes, #BrighttStepPath is predominantly a recruitment and people development business, ran by me dedicated to training & assisting others in achieving extra income (pt or f/t) around their current commitments, people also have the opportunity to build their own business brand with my support. My brand colours are Red, White and Black, and I would like to incorporate the following text;

#BrightStepPath

Recruiting now! Start today & start earning!

Would you like an extra income, for…
A holiday?…A new car?…Lifestyle changes?
(Can you put a tick box or something similar adjacent to each)

Are you facing…
Redundancy? Birth of a new child? Hefty bills?

If so, I have the solution.

Contact Yvonne Darcott today: (can you insert the appropriate icon for each of the contact details)
Tel: 07419 604172
Twitter: @Bright_StepPath
Email: Yvonne@brightsteppath-example.co.uk
Facebook: www.facebook-example.com/yvonbrightsteppath

Target Market(s)

Women aged 25-45 years, possibly busy mums too, wanting to earn additinal income to allow them more choices, be it family time, money, new challenge, meeting new people, personal development

Industry/Entity Type

Health And Wellness

Font styles to use
Serif
Sans Serif
Decorative
Script

Colors
ec1f27
ffffff
000000

Requirements
Must have
• My heels logo, be clear concise and eye catching, I also have the following strap line if you wish to use;
• Empowering other to achieve
• Also I have attached a closeup picture of myself but would ideally only like half my face to appear (leftside) similar to the other picture posted - if you can
Nice to have
• Perhaps adding other forms of graphics, or the 3rd picture I have attached with myself...possibly just the shoes though
Should not have
• Too many colours

```html
<!DOCTYPE html>
<html lang="en">
<head>
<meta charset="utf-8">
<title>Bright Step Path Flyer</title>
<link rel="stylesheet" href="https://fonts.googleapis.com/css2?family=Poiret+One&family=Josefin+Sans:wght@300;400;700&family=Oswald:wght@500;600&family=Roboto+Condensed:wght@700&display=swap">
<style>
  :root {
    --red: #ec1f27;
    --white: #ffffff;
    --black: #000000;
    --ink: #1b1b1b;
    --cream: #efedd9;
    --grey: #c9c9c9;
  }
  * { margin: 0; padding: 0; box-sizing: border-box; }
  html, body { width: 900px; height: 1200px; overflow: hidden; background: var(--cream); }
  .flyer { position: relative; width: 900px; height: 1200px; }
  .sheet { position: absolute; left: 48px; top: 24px; width: 804px; height: 1148px; background: var(--white); overflow: hidden; }
  .portrait { position: absolute; left: 0; top: 0; width: 424px; height: 1148px; }
  .recruiting {
    position: absolute; left: 327px; top: 600px;
    transform: translate(-50%, -50%) rotate(-90deg);
    font-family: "Poiret One", sans-serif; font-size: 64px; color: var(--black);
    white-space: nowrap; letter-spacing: 1px;
  }
  .chevron { position: absolute; left: 398px; top: 560px; }
  .contact-list { position: absolute; left: 42px; top: 970px; list-style: none; }
  .contact-list li {
    display: flex; align-items: center; gap: 8px; height: 30px;
    font-family: "Roboto Condensed", sans-serif; font-weight: 700; font-size: 20px; color: var(--white);
  }
  .contact-list svg { flex: none; }
  .side { position: absolute; left: 440px; top: 0; width: 364px; text-align: center; color: var(--ink); }
  .owner {
    position: absolute; left: 0; right: 0; top: 36px;
    font-family: "Poiret One", sans-serif; font-size: 54px; line-height: 52px;
    transform: scaleY(1.5); transform-origin: top; color: var(--black); font-weight: 400;
  }
  .heels-mark {
    position: absolute; left: 52px; top: 192px; width: 250px; height: 236px;
    background: linear-gradient(135deg, #fafafa 0%, #f0f0f0 55%, #e8e8e8 100%);
  }
  .tag { position: absolute; left: 0; right: 0; top: 430px; font-family: "Josefin Sans", sans-serif; font-weight: 700; font-size: 31px; color: var(--black); }
  .strap { position: absolute; left: 0; right: 0; top: 466px; font-family: "Josefin Sans", sans-serif; font-weight: 300; font-size: 20px; color: var(--ink); }
  .start { position: absolute; left: 0; right: 0; top: 518px; font-family: "Josefin Sans", sans-serif; font-weight: 300; font-size: 31px; line-height: 38px; color: var(--black); }
  .question { position: absolute; left: 0; right: 0; font-family: "Oswald", sans-serif; font-weight: 600; font-size: 18px; color: var(--black); }
  .q-income { top: 634px; }
  .q-facing { top: 821px; }
  .options { position: absolute; left: 14px; width: 336px; display: flex; justify-content: space-between; list-style: none; }
  .options-income { top: 670px; }
  .options-facing { top: 858px; }
  .option { width: 108px; display: flex; flex-direction: column; align-items: center; }
  .option .label { margin-top: 6px; font-family: "Oswald", sans-serif; font-weight: 500; font-size: 12.5px; line-height: 15px; color: var(--black); }
  .option .tick { margin-top: 4px; width: 12px; height: 12px; border: 1px solid #444; border-radius: 50%; }
  .cta { position: absolute; left: 0; right: 0; top: 1020px; color: var(--black); }
  .cta .word { font-family: "Oswald", sans-serif; font-weight: 600; font-size: 23px; line-height: 30px; }
  .cta .name { font-family: "Poiret One", sans-serif; font-size: 30px; line-height: 42px; transform: scaleY(1.4); }
</style>
</head>
<body>
<main class="flyer">
  <section class="sheet">
    <svg class="portrait" viewBox="0 0 424 1148" role="img" aria-label="Portrait photograph of the business owner in profile, light curtain behind, dark top">
      <defs>
        <linearGradient id="photoTone" x1="0" y1="0" x2="0" y2="1">
          <stop offset="0" stop-color="#ecebe8"/>
          <stop offset="0.3" stop-color="#b9aaa0"/>
          <stop offset="0.5" stop-color="#4a4240"/>
          <stop offset="0.75" stop-color="#111"/>
          <stop offset="1" stop-color="#000"/>
        </linearGradient>
        <linearGradient id="foldShade" x1="0" y1="0" x2="1" y2="0">
          <stop offset="0" stop-color="#b5b5b5"/>
          <stop offset="1" stop-color="#ffffff"/>
        </linearGradient>
      </defs>
      <rect width="424" height="1148" fill="url(#photoTone)"/>
      <path d="M424 300 C 250 360, 170 520, 190 650 C 210 800, 300 900, 424 990 Z" fill="var(--white)"/>
      <path d="M236 390 C 215 470, 215 640, 240 760 L 252 760 C 230 640, 230 470, 250 390 Z" fill="url(#foldShade)"/>
    </svg>

    <div class="recruiting">RECRUITING NOW!</div>
    <svg class="chevron" width="40" height="48" viewBox="0 0 40 48" aria-hidden="true">
      <path d="M4 4 L32 24 L4 44" fill="none" stroke="#cfcfcf" stroke-width="9"/>
    </svg>

    <ul class="contact-list">
      <li>
        <svg width="20" height="20" viewBox="0 0 20 20" aria-hidden="true"><circle cx="10" cy="10" r="8.5" fill="none" stroke="var(--white)" stroke-width="1.5"/><path d="M7 5.5 L8.5 8 L7.6 9 C8.3 10.6 9.4 11.7 11 12.4 L12 11.5 L14.5 13 L13.5 14.6 C9.5 14.3 5.8 10.5 5.5 6.5 Z" fill="var(--white)"/></svg>
        07419 604172
      </li>
      <li>
        <svg width="20" height="16" viewBox="0 0 20 16" aria-hidden="true"><rect x="1" y="2" width="18" height="12" fill="none" stroke="var(--white)" stroke-width="1.5"/><path d="M1 2 L10 9 L19 2" fill="none" stroke="var(--white)" stroke-width="1.5"/></svg>
        Yvonne@brightsteppath-example.co.uk
      </li>
      <li>
        <svg width="18" height="18" viewBox="0 0 18 18" aria-hidden="true"><rect width="18" height="18" rx="2" fill="#4a90d9"/></svg>
        @Bright_StepPath
      </li>
      <li>
        <svg width="18" height="18" viewBox="0 0 18 18" aria-hidden="true"><rect width="18" height="18" rx="2" fill="#4a67a8"/></svg>
        yvonbrightsteppath
      </li>
    </ul>

    <div class="side">
      <h1 class="owner">YVONNE<br>DARCOTT'S</h1>
      <div class="heels-mark" role="img" aria-label="Hand-drawn illustration of two high heels with red soles"></div>
      <p class="tag">#BrightStepPath</p>
      <p class="strap">Empowering other to achieve</p>
      <p class="start">START TODAY<br>START EARNING!</p>

      <h2 class="question q-income">WOULD YOU LIKE AN EXTRA INCOME FOR</h2>
      <ul class="options options-income">
        <li class="option">
          <svg width="88" height="88" viewBox="0 0 88 88" aria-hidden="true"><circle cx="44" cy="44" r="41" fill="none" stroke="var(--ink)" stroke-width="3"/>
            <path d="M24 38 A20 14 0 0 1 64 38 Z" fill="var(--red)"/><line x1="44" y1="38" x2="38" y2="62" stroke="var(--red)" stroke-width="3"/>
            <path d="M22 62 L62 62 L66 54" fill="none" stroke="var(--red)" stroke-width="3.5"/><line x1="26" y1="62" x2="24" y2="68" stroke="var(--red)" stroke-width="3"/><line x1="58" y1="62" x2="60" y2="68" stroke="var(--red)" stroke-width="3"/></svg>
          <span class="label">A HOLIDAY?</span><span class="tick"></span>
        </li>
        <li class="option">
          <svg width="88" height="88" viewBox="0 0 88 88" aria-hidden="true"><circle cx="44" cy="44" r="41" fill="none" stroke="var(--ink)" stroke-width="3"/>
            <path d="M26 46 L31 32 L57 32 L62 46 L62 58 L26 58 Z" fill="var(--red)"/><rect x="34" y="36" width="20" height="9" fill="var(--white)"/>
            <circle cx="32" cy="51" r="3" fill="var(--white)"/><circle cx="56" cy="51" r="3" fill="var(--white)"/>
            <rect x="27" y="58" width="7" height="6" fill="var(--red)"/><rect x="54" y="58" width="7" height="6" fill="var(--red)"/></svg>
          <span class="label">A NEW CAR?</span><span class="tick"></span>
        </li>
        <li class="option">
          <svg width="88" height="88" viewBox="0 0 88 88" aria-hidden="true"><circle cx="44" cy="44" r="41" fill="none" stroke="var(--ink)" stroke-width="3"/>
            <circle cx="44" cy="40" r="6" fill="var(--red)"/><path d="M33 66 L33 54 C33 49 55 49 55 54 L55 66 Z" fill="var(--red)"/>
            <path d="M33 54 L24 44 M55 54 L64 44" stroke="var(--red)" stroke-width="3"/>
            <circle cx="28" cy="28" r="4" fill="var(--red)"/><rect x="40" y="20" width="8" height="6" fill="var(--red)"/><circle cx="60" cy="27" r="4" fill="var(--red)"/></svg>
          <span class="label">LIFESTYLE CHANGES?</span><span class="tick"></span>
        </li>
      </ul>

      <h2 class="question q-facing">ARE YOU FACING...</h2>
      <ul class="options options-facing">
        <li class="option">
          <svg width="88" height="88" viewBox="0 0 88 88" aria-hidden="true"><circle cx="44" cy="44" r="41" fill="none" stroke="var(--ink)" stroke-width="3"/>
            <text x="44" y="41" text-anchor="middle" font-family="Oswald, sans-serif" font-weight="600" font-size="22" fill="var(--red)">NO</text>
            <text x="44" y="64" text-anchor="middle" font-family="Oswald, sans-serif" font-weight="600" font-size="22" fill="var(--red)">JOB</text></svg>
          <span class="label">REDUNCANCY?</span><span class="tick"></span>
        </li>
        <li class="option">
          <svg width="88" height="88" viewBox="0 0 88 88" aria-hidden="true"><circle cx="44" cy="44" r="41" fill="none" stroke="var(--ink)" stroke-width="3"/>
            <circle cx="42" cy="20" r="5" fill="var(--red)"/><path d="M37 28 L47 28 C52 34 54 42 49 48 L47 56 L37 56 Z" fill="var(--red)"/>
            <rect x="38" y="56" width="3.5" height="18" fill="var(--red)"/><rect x="43" y="56" width="3.5" height="18" fill="var(--red)"/></svg>
          <span class="label">BIRTH OF A<br>NEW CHILD?</span><span class="tick"></span>
        </li>
        <li class="option">
          <svg width="88" height="88" viewBox="0 0 88 88" aria-hidden="true"><circle cx="44" cy="44" r="41" fill="none" stroke="var(--ink)" stroke-width="3"/>
            <rect x="30" y="24" width="30" height="38" fill="var(--white)" stroke="var(--red)" stroke-width="2.5"/>
            <rect x="24" y="30" width="30" height="38" fill="var(--white)" stroke="var(--red)" stroke-width="2.5"/>
            <circle cx="46" cy="39" r="5" fill="var(--red)"/><path d="M29 37 H39 M29 43 H39 M29 50 H49 M29 56 H49 M29 62 H49" stroke="var(--red)" stroke-width="2"/></svg>
          <span class="label">HEFTY BILLS?</span><span class="tick"></span>
        </li>
      </ul>

      <div class="cta">
        <p class="word">CONTACT</p>
        <p class="name">YVONNE DARCOTT</p>
        <p class="word">TODAY</p>
      </div>
    </div>
  </section>
</main>
</body>
</html>
```